Business Card for a New Zealand IT Startup

I need a business card for VELTA Holdings. We are a young startup based in New Zealand working in internet marketing and web development. The design should have some element connected to New Zealand, such as wave, koru or silver fern, just don't use a kiwi bird.

```html
<!DOCTYPE html>
<html lang="en">
<head>
<meta charset="utf-8">
<title>VELTA Holdings – Business Card</title>
<link href="https://fonts.googleapis.com/css2?family=Open+Sans:ital,wght@1,400&family=Roboto:ital,wght@0,400;0,700;1,300&display=swap" rel="stylesheet">
<style>
  :root {
    --canvas: #ffffff;
    --label-blue: #1f6fb5;
    --brand-blue: #0b6fb8;
    --brand-orange: #e8632b;
    --slate-top: #5b6673;
    --slate-bottom: #6e7b88;
    --card-orange: #df5f31;
    --mist-light: #e4e4e7;
    --mist-dark: #cfd0d3;
    --bronze-light: #c99b40;
    --bronze-mid: #a87a30;
    --bronze-dark: #7d5620;
    --white: #ffffff;
  }
  * { margin: 0; padding: 0; box-sizing: border-box; }
  html, body {
    width: 1200px; height: 1200px; overflow: hidden;
    background: var(--canvas);
  }
  .sheet { position: relative; width: 1200px; height: 1200px; }

  .side-label {
    position: absolute; left: 0; width: 1200px; text-align: center;
    font-family: "Open Sans", sans-serif; font-style: italic;
    font-size: 20px; color: var(--label-blue);
  }
  .side-label--front { top: 134px; }
  .side-label--back { top: 1042px; }

  .card { position: absolute; left: 248px; width: 704px; overflow: hidden; }

  /* Front */
  .card--front { top: 170px; height: 422px; }
  .front-backdrop {
    position: absolute; inset: 0;
    background:
      radial-gradient(ellipse 60% 45% at 25% 20%, var(--mist-dark) 0%, rgba(207,208,211,0) 100%),
      radial-gradient(ellipse 50% 40% at 75% 15%, #d6d5d6 0%, rgba(214,213,214,0) 100%),
      var(--mist-light);
  }
  .brand-lockup {
    position: absolute; left: 0; right: 0; top: 176px;
    display: flex; align-items: center; justify-content: center; gap: 20px;
  }
  .brand-dot {
    width: 30px; height: 30px; border-radius: 50%;
    background: var(--brand-orange);
  }
  .brand-name {
    font-family: "Roboto", sans-serif; font-weight: 700;
    font-size: 66px; line-height: 1; color: var(--brand-blue);
    letter-spacing: 1px;
  }

  /* Back */
  .card--back { top: 605px; height: 422px; }
  .back-upper {
    position: absolute; left: 0; top: 0; width: 100%; height: 249px;
    background: linear-gradient(180deg, var(--slate-top), var(--slate-bottom));
  }
  .back-lower {
    position: absolute; left: 0; top: 249px; width: 100%; height: 173px;
    background: var(--card-orange);
  }
  .koru-photo {
    position: absolute; left: 400px; top: 40px; width: 240px; height: 382px;
    background:
      radial-gradient(ellipse 50% 34% at 58% 30%, var(--bronze-light) 0%, var(--bronze-mid) 45%, rgba(125,86,32,0.6) 75%, rgba(125,86,32,0) 100%),
      radial-gradient(ellipse 40% 45% at 40% 78%, rgba(168,122,48,0.35) 0%, rgba(168,122,48,0) 100%);
  }
  .holder-name {
    position: absolute; left: 92px; top: 74px;
    font-family: "Roboto", sans-serif; font-weight: 700;
    font-size: 62px; line-height: 1; color: var(--white);
  }
  .holder-role {
    position: absolute; left: 92px; top: 135px;
    font-family: "Roboto", sans-serif; font-weight: 300; font-style: italic;
    font-size: 26px; line-height: 1; color: var(--white);
  }
  .contact-list {
    position: absolute; left: 92px; top: 258px; list-style: none;
    font-family: "Roboto", sans-serif; font-size: 19px; color: var(--white);
  }
  .contact-item { display: flex; align-items: center; gap: 11px; height: 29px; }
  .contact-icon { width: 19px; height: 19px; flex: none; }
  .contact-web { margin-top: 10px; }
</style>
</head>
<body>
<div class="sheet">
  <p class="side-label side-label--front">front</p>

  <section class="card card--front">
    <div class="front-backdrop" role="img" aria-label="Soft, faded photograph of New Zealand silver fern fronds"></div>
    <div class="brand-lockup">
      <span class="brand-dot"></span>
      <span class="brand-name">VELTA Holdings</span>
    </div>
  </section>

  <section class="card card--back">
    <div class="back-upper"></div>
    <div class="back-lower"></div>
    <div class="koru-photo" role="img" aria-label="Photograph of an unfurling New Zealand koru fern frond in bronze tones, its stem fading into the orange band"></div>

    <h1 class="holder-name">Liam Carter</h1>
    <p class="holder-role">company position</p>

    <ul class="contact-list">
      <li class="contact-item">
        <svg class="contact-icon" viewBox="0 0 24 24"><path fill="#fff" d="M6.6 10.8a15 15 0 0 0 6.6 6.6l2.2-2.2c.3-.3.7-.4 1-.2 1.1.4 2.3.6 3.6.6.6 0 1 .4 1 1V20c0 .6-.4 1-1 1A17 17 0 0 1 3 4c0-.6.4-1 1-1h3.5c.6 0 1 .4 1 1 0 1.3.2 2.5.6 3.6.1.3 0 .7-.2 1z"/></svg>
        <span>0800-372916</span>
      </li>
      <li class="contact-item">
        <svg class="contact-icon" viewBox="0 0 24 24"><rect x="2" y="5" width="20" height="14" fill="#fff"/><path d="M2 5l10 8 10-8" fill="none" stroke="var(--card-orange)" stroke-width="1.6"/></svg>
        <span>liamcarter@veltaholdings.com</span>
      </li>
      <li class="contact-item contact-web"><span>www.veltaholdings.com</span></li>
    </ul>
  </section>

  <p class="side-label side-label--back">back</p>
</div>
</body>
</html>
```